Business Card for Fashion House

We need a business card design for our personalize fashion service for our customers. the business card should reflect reliability, luxury and creativity.
The brand Gravetto is extracted from "Graceful Velvetto"; Gravetto provides fashion designs sprinkled with luxury and style tailored for our elite clients character profile.
Gravetto is created for those who embody class and elegance with a passion for style.
Target Market(s)
Affluent Customers
Industry/Entity Type
Fashion
Contact Information for Business Card
Samira Haddadin
Fashion Designer
Telephone: +971 4 555 0192
Mobile +971 50 555 0147
Emal info@gravetto-example.com
Website www.gravetto-example.com
Social Media Youtube g+ Facebook Instagram Pin /gravetto
Font styles to use
Other font styles liked:
- Audrey provided
Look and feel
Each slider illustrates characteristics of the customer's brand and the style your logo design should communicate.

```html
<!DOCTYPE html>
<html lang="en">
<head>
<meta charset="utf-8">
<title>Gravetto Business Card</title>
<link rel="stylesheet" href="https://fonts.googleapis.com/css2?family=Marcellus&family=Alegreya+Sans:wght@400;700&display=swap">
<style>
  :root {
    --backdrop: #3b322e;
    --ink: #0d0d0d;
    --paper: #ffffff;
    --silver: #9a9a9a;
    --band-text: #e6e6e6;
    --body-text: #1a1a1a;
  }
  * { box-sizing: border-box; margin: 0; padding: 0; }
  html, body { width: 1200px; height: 780px; overflow: hidden; }
  body {
    background: var(--backdrop);
    font-family: "Alegreya Sans", sans-serif;
    position: relative;
  }
  .card {
    position: absolute;
    top: 247px;
    width: 510px;
    height: 286px;
    box-shadow: 0 14px 30px rgba(0,0,0,0.45);
  }
  .card-front {
    left: 60px;
    background: var(--ink);
    display: flex;
    align-items: center;
    justify-content: center;
  }
  .front-wordmark {
    font-family: "Marcellus", serif;
    font-size: 30px;
    letter-spacing: 12px;
    color: var(--silver);
    text-transform: uppercase;
    padding-left: 12px;
  }
  .card-back {
    left: 630px;
    background: var(--paper);
    display: flex;
  }
  .brand-band {
    width: 62px;
    height: 100%;
    background: var(--ink);
    position: relative;
  }
  .band-wordmark {
    position: absolute;
    left: 50%;
    top: 50%;
    transform: translate(-50%, -50%) rotate(-90deg);
    font-family: "Marcellus", serif;
    font-size: 26px;
    letter-spacing: 10px;
    color: var(--band-text);
    text-transform: uppercase;
    white-space: nowrap;
  }
  .details {
    flex: 1;
    position: relative;
    padding: 118px 0 0 22px;
    color: var(--body-text);
  }
  .holder-name { font-size: 17px; font-weight: 700; line-height: 1; }
  .holder-role { font-size: 13px; margin-top: 2px; margin-bottom: 12px; }
  .contact-list { list-style: none; font-size: 14px; line-height: 19px; }
  .contact-list li { display: flex; align-items: center; gap: 7px; }
  .contact-list svg { width: 14px; height: 14px; flex: none; }
  .contact-web { font-size: 13px; letter-spacing: 1px; margin-top: 2px; }
  .social {
    position: absolute;
    right: 22px;
    bottom: 22px;
    display: flex;
    align-items: center;
    gap: 6px;
    font-family: "Marcellus", serif;
    font-size: 13px;
    letter-spacing: 3px;
  }
  .social-dot {
    width: 16px; height: 16px;
    border: 1.5px solid var(--body-text);
    border-radius: 50%;
  }
</style>
</head>
<body>
  <section class="card card-front">
    <span class="front-wordmark">Gravetto</span>
  </section>

  <section class="card card-back">
    <div class="brand-band">
      <span class="band-wordmark">Gravetto</span>
    </div>
    <div class="details">
      <p class="holder-name">Samira Haddadin</p>
      <p class="holder-role">Fashion Designer</p>
      <ul class="contact-list">
        <li>
          <svg viewBox="0 0 14 14" aria-hidden="true"><circle cx="7" cy="7" r="6.3" fill="none" stroke="#1a1a1a"/><path d="M4.5 5.5c.5 2 2 3.5 4 4l1-1-1.2-.8-.7.5c-.8-.4-1.4-1-1.8-1.8l.5-.7-.8-1.2z" fill="#1a1a1a"/></svg>
          +971 4 555 0192
        </li>
        <li>
          <svg viewBox="0 0 14 14" aria-hidden="true"><circle cx="7" cy="7" r="6.3" fill="none" stroke="#1a1a1a"/><rect x="5" y="3.5" width="4" height="7" rx="0.7" fill="none" stroke="#1a1a1a"/></svg>
          +971 50 555 0147
        </li>
        <li>
          <svg viewBox="0 0 14 14" aria-hidden="true"><circle cx="7" cy="7" r="6.3" fill="none" stroke="#1a1a1a"/><rect x="3.8" y="4.8" width="6.4" height="4.4" fill="none" stroke="#1a1a1a"/><path d="M3.8 4.8L7 7.3l3.2-2.5" fill="none" stroke="#1a1a1a"/></svg>
          info@gravetto-example.com
        </li>
        <li class="contact-web">
          <svg viewBox="0 0 14 14" aria-hidden="true"><circle cx="7" cy="7" r="6.3" fill="none" stroke="#1a1a1a"/><circle cx="7" cy="7" r="3.5" fill="none" stroke="#1a1a1a"/><path d="M3.5 7h7M7 3.5v7" stroke="#1a1a1a"/></svg>
          www.gravetto-example.com
        </li>
      </ul>
      <div class="social">
        <span class="social-dot"></span>
        <span>/gravetto</span>
      </div>
    </div>
  </section>
</body>
</html>
```